Website redesign - vorelmik.com

We are looking to do a full redesign of vorelmik.com. Need a designer to come up overall layout and 3 specific pages and 3 different hero images.
Wireframes for the 3 pages are attached as well as site images. You don't have to follow the wireframes exactly, but instead the wireframe is there to show you the information that needs to be on each page. Feel free to rearrange as needed.
Our target market is self taught engineers. So definitely I want a more casual feel to it. I'm ok with fun bold colors as well. Really like websites that have the infinite scroll look/feel to them.
Looking to find a designer who will produce HTML and potentially even implement the HTML into our site checked in code.
HTML Code should be responsive/mobile first leveraging Bootstrap 4.
Attached files include:
0) Wireframe PDF
https://files.plomwerk.net/d/7Kx2pQmW9zLr4TbN8vYc3HsE5fJ/view?mode=share
1) Vorelmik Images zip 1
https://files.plomwerk.net/d/4Gt8nRvB2wQx6MkZ1pLd9YaC7hU/view?mode=share
2) Vorelmik Images zip 2
https://files.plomwerk.net/d/9Jw3sTcF5yNv1HqX8rKb2ZeM6dP/view?mode=share
Target Market(s)
I sell DIY Waterproof Electronics enclosures. Target audience is self taught DIY engineers
Coding
Coded - Design and coding required
Number of Pages Required
3 page
Colors
Designer to choose colors to be used in the design.
Look and feel

```html
<!DOCTYPE html>
<html lang="en">
<head>
<meta charset="utf-8">
<title>Vorelmik – Waterproof Project Boxes</title>
<link href="https://fonts.googleapis.com/css2?family=Roboto:ital,wght@0,400;0,500;0,700;1,400;1,500&family=Montserrat:wght@600;700&display=swap" rel="stylesheet">
<style>
:root{
  --blue:#1533f0;
  --blue-deep:#0b2bd6;
  --gold:#e6bc14;
  --gold-band:#d6ad18;
  --ink:#222;
  --muted:#444;
  --grey-band:#eeeff1;
  --footer:#131313;
  --white:#fff;
}
*{box-sizing:border-box;margin:0;padding:0}
html,body{width:1200px;height:3690px;overflow:hidden}
body{position:relative;font-family:"Roboto",sans-serif;color:var(--ink);background:var(--white)}
.abs{position:absolute}
.btn{position:absolute;display:flex;align-items:center;justify-content:center;background:var(--gold);border:2px solid #b38f07;font-family:"Montserrat",sans-serif;font-weight:700;font-size:15px;color:#222;text-transform:uppercase;text-decoration:none}
.media{position:absolute;border:5px solid #fff;box-shadow:0 6px 18px rgba(0,0,0,.18)}

/* header */
.site-header{position:absolute;left:0;top:0;width:1200px;height:87px;border-top:4px solid var(--gold);background:#fff}
.brand{position:absolute;left:112px;top:20px;font-size:42px;font-weight:700;color:var(--blue);letter-spacing:-.5px}
.nav a{position:absolute;top:38px;font-size:15px;color:#222;text-decoration:none}
.nav a.active{color:var(--blue)}
.auth{position:absolute;top:26px;height:40px;display:flex;align-items:center;justify-content:center;font-family:"Montserrat",sans-serif;font-weight:600;font-size:14px}
.auth.sign-in{left:912px;width:83px;background:var(--blue);color:#fff}
.auth.sign-up{left:1004px;width:84px;background:var(--gold);color:#222}

/* hero */
.hero{position:absolute;left:0;top:87px;width:1200px;height:451px;background:linear-gradient(110deg,#2a4bf5 0%,#1637ee 55%,#0e2ae0 100%);overflow:hidden}
.hero-photo{position:absolute;left:57px;top:28px;width:444px;height:393px;background:radial-gradient(ellipse at 50% 50%,#7d7a6e 0%,#4e5060 55%,rgba(40,60,200,0) 75%)}
.hero h1{position:absolute;left:617px;top:99px;width:480px;font-size:39px;line-height:43px;font-weight:500;color:#fff}
.hero .tag{position:absolute;left:620px;top:244px;font-family:"Montserrat",sans-serif;font-weight:700;font-size:20px;color:var(--gold)}
.hero .btn{left:623px;top:284px;width:153px;height:47px}
.slide-arrow{position:absolute;width:56px;height:56px;border:2px solid #fff;border-radius:50%}
.slide-arrow svg{position:absolute;left:18px;top:17px}

/* designer */
.designer h2{position:absolute;right:662px;top:606px;text-align:right;font-size:34px;line-height:40px;font-weight:400;color:#222}
.designer h2 b{font-weight:700}
.designer .btn{left:385px;top:706px;width:155px;height:47px}
.video{left:601px;top:600px;width:483px;height:275px;background:linear-gradient(135deg,#8f8a80,#4b4038 60%,#6a5a44)}
.play{position:absolute;left:209px;top:105px;width:62px;height:62px;border-radius:50%;background:#c9a216;border:2px solid #fff}

/* mounting kits */
.kits{position:absolute;left:0;top:955px;width:1200px;height:434px;background:var(--grey-band)}
.panel-side{position:absolute;top:75px;height:277px;width:107px;background:#5b5c60}
.panel-main{position:absolute;left:196px;top:73px;width:297px;height:279px;background:#fff;border:9px solid #d8d8d8}
.box-shot{position:absolute;left:54px;top:42px;width:172px;height:178px;border-radius:10px;background:linear-gradient(160deg,#cfc8ff,#a79cf0)}
.kits h2{position:absolute;left:654px;top:83px;width:420px;font-size:34px;line-height:39px;font-weight:500;color:#222}
.kits .btn{left:654px;top:256px;width:155px;height:46px}

/* makers */
.makers h3{position:absolute;left:112px;top:1478px;font-size:21px;line-height:30px;font-weight:500;color:#222}
.features{position:absolute;left:163px;top:1563px;list-style:none;font-size:15px;color:#333}
.features li{position:relative;padding-left:27px;height:34.4px;line-height:22px}
.features li svg{position:absolute;left:0;top:4px}
.makers .btn{left:163px;top:1760px;width:155px;height:46px}
.kit-photo{left:624px;top:1485px;width:461px;height:315px;background:linear-gradient(135deg,#7e6a52,#a88c68 50%,#5d503f)}

/* testimonials */
.reviews{position:absolute;left:0;top:1885px;width:1200px;height:433px;background:var(--gold-band)}
.reviews h2{position:absolute;left:0;width:1200px;top:52px;text-align:center;font-size:34px;font-weight:500;color:#222}
.quote{position:absolute;top:141px;width:436px;height:211px;padding:34px 38px 0 38px;font-style:italic;font-size:14px;line-height:30px}
.quote.blue{left:146px;background:var(--blue);color:#fff}
.quote.white{left:617px;background:#fff;color:#555}
.stars{display:flex;gap:3px;margin-top:4px}
.quote .who{font-weight:500;font-size:16px;margin-top:8px}
.quote.white .who{color:#222}
.big-mark{position:absolute;right:18px;bottom:12px;font-family:"Roboto",sans-serif;font-style:normal;font-weight:700;font-size:170px;line-height:120px;opacity:.18}

/* examples */
.examples h2{position:absolute;left:0;width:1200px;top:2374px;text-align:center;font-size:34px;font-weight:500;color:#222}
.card{position:absolute;width:301px}
.card .shot{height:271px;border:1px solid #ddd;display:flex;align-items:center;justify-content:center;background:#fff}
.card .shot div{width:235px;height:160px;border-radius:6px}
.card .name{margin:22px 0 0 20px;font-size:16px;font-weight:500;color:#222;line-height:22px}
.card .sub{margin-left:20px;font-size:15px;color:#333}

/* footer */
.site-footer{position:absolute;left:0;top:3610px;width:1200px;height:80px;background:var(--footer);color:#fff}
.site-footer .copy{position:absolute;left:112px;top:28px;font-size:17px}
.site-footer .follow{position:absolute;left:891px;top:28px;font-size:17px}
.social{position:absolute;top:19px;width:41px;height:41px;border:2px solid #fff;border-radius:50%}
</style>
</head>
<body>

<header class="site-header">
  <div class="brand">Vorelmik</div>
  <nav class="nav">
    <a class="active" style="left:388px">Get Started</a>
    <a style="left:510px">Designs</a>
    <a style="left:607px">FAQs</a>
    <a style="left:687px">Videos</a>
    <a style="left:779px">Contact Us</a>
  </nav>
  <div class="auth sign-in">SIGN IN</div>
  <div class="auth sign-up">SIGN UP</div>
</header>

<section class="hero">
  <div class="hero-photo" role="img" aria-label="Assembled electronics mounting plate with terminal boards and wiring"></div>
  <h1>Waterproof Project Boxes Customized to your Exact Needs</h1>
  <div class="tag">(AT A FRACTION OF THE PRICE)</div>
  <a class="btn">Get Started</a>
  <div class="slide-arrow" style="left:21px;top:204px"><svg width="18" height="20" viewBox="0 0 18 20"><path d="M12 2 4 10l8 8" fill="none" stroke="#fff" stroke-width="2.5"/></svg></div>
  <div class="slide-arrow" style="left:1113px;top:204px"><svg width="18" height="20" viewBox="0 0 18 20"><path d="M6 2l8 8-8 8" fill="none" stroke="#fff" stroke-width="2.5"/></svg></div>
</section>

<section class="designer">
  <h2><b>Customize your Project</b><br>Box using our Designer</h2>
  <a class="btn">Get Started</a>
  <div class="media video" role="img" aria-label="Video still of a grey waterproof box mounted outdoors beside a brick wall">
    <div class="play"><svg width="62" height="62" viewBox="0 0 62 62" style="position:absolute;left:-2px;top:-2px"><path d="M26 22l14 9-14 9z" fill="#fff"/></svg></div>
  </div>
</section>

<section class="kits">
  <div class="panel-side" style="left:89px"></div>
  <div class="panel-side" style="left:489px"></div>
  <svg class="abs" style="left:152px;top:186px" width="48" height="26" viewBox="0 0 48 26"><path d="M46 13H4M14 2 3 13l11 11" fill="none" stroke="#fff" stroke-width="2.5"/></svg>
  <svg class="abs" style="left:492px;top:186px" width="48" height="26" viewBox="0 0 48 26"><path d="M2 13h42M34 2l11 11-11 11" fill="none" stroke="#fff" stroke-width="2.5"/></svg>
  <div class="panel-main"><div class="box-shot" role="img" aria-label="Translucent lavender waterproof enclosure"></div></div>
  <h2>Mounting Kits for all the popular water proof project boxes with many sizes to choose from</h2>
  <a class="btn">Get Started</a>
</section>

<section class="makers">
  <h3>Vorelmik waterproof project boxes<br>were built by makers for makers</h3>
  <ul class="features">
    <li><svg width="14" height="14" viewBox="0 0 14 14"><circle cx="7" cy="7" r="6" fill="none" stroke="#d6ad18" stroke-width="1.6"/><path d="M4 7l2 2 4-4" fill="none" stroke="#d6ad18" stroke-width="1.6"/></svg>Design to your specifications</li>
    <li style="height:68.8px"><svg width="14" height="14" viewBox="0 0 14 14"><circle cx="7" cy="7" r="6" fill="none" stroke="#d6ad18" stroke-width="1.6"/><path d="M4 7l2 2 4-4" fill="none" stroke="#d6ad18" stroke-width="1.6"/></svg>Maker components: Tinkerduo, Quillberry Pi,<br><span style="line-height:46px">Steadvolt Power</span></li>
    <li><svg width="14" height="14" viewBox="0 0 14 14"><circle cx="7" cy="7" r="6" fill="none" stroke="#d6ad18" stroke-width="1.6"/><path d="M4 7l2 2 4-4" fill="none" stroke="#d6ad18" stroke-width="1.6"/></svg>Detailed build instructions, videos, walkthroughs</li>
    <li><svg width="14" height="14" viewBox="0 0 14 14"><circle cx="7" cy="7" r="6" fill="none" stroke="#d6ad18" stroke-width="1.6"/><path d="M4 7l2 2 4-4" fill="none" stroke="#d6ad18" stroke-width="1.6"/></svg>DIY made to look professional</li>
  </ul>
  <a class="btn">Get Started</a>
  <div class="media kit-photo" role="img" aria-label="Hardboard mounting plates with controller boards, power supply and hardware bag on a workbench"></div>
</section>

<section class="reviews">
  <h2>What our Customers Have to Say</h2>
  <div class="quote blue">
    <div>&#8220; Great work at a reasonable cost.I can't recommend them enough. If you're doing custom boxes forlight shows, this is where you go. &#8221;</div>
    <div class="stars"><svg width="82" height="14" viewBox="0 0 82 14"><g fill="#e6bc14"><path id="s" d="M7 0l2 4.6 5 .4-3.8 3.2 1.2 4.8L7 10.4 2.6 13l1.2-4.8L0 5l5-.4z"/><use href="#s" x="16"/><use href="#s" x="32"/><use href="#s" x="48"/></g><use href="#s" x="64" fill="none" stroke="#e6bc14"/></svg></div>
    <div class="who">- Marta K</div>
    <div class="big-mark" style="color:#0a1aa8;opacity:.5">&#8221;</div>
  </div>
  <div class="quote white">
    <div>&#8220; Fantastic service/product..whether you simply generate the design and do all of the fabrication yourself or simply order the kits. &#8221;</div>
    <div class="stars"><svg width="82" height="14" viewBox="0 0 82 14"><g fill="#e6bc14"><path id="t" d="M7 0l2 4.6 5 .4-3.8 3.2 1.2 4.8L7 10.4 2.6 13l1.2-4.8L0 5l5-.4z"/><use href="#t" x="16"/><use href="#t" x="32"/><use href="#t" x="48"/></g><use href="#t" x="64" fill="none" stroke="#e6bc14"/></svg></div>
    <div class="who">- Dion F</div>
    <div class="big-mark" style="color:#999">&#8221;</div>
  </div>
</section>

<section class="examples">
  <h2>See Real Examples from our Customers</h2>
  <div class="card" style="left:111px;top:2462px"><div class="shot"><div role="img" aria-label="Controller boards on a black mounting plate" style="background:linear-gradient(135deg,#3b5e47,#2a2a2a)"></div></div><div class="name">KVX RB8-72 w/ P16v3 +</div><div class="sub">Expansion board</div></div>
  <div class="card" style="left:449px;top:2462px"><div class="shot"><div role="img" aria-label="Terminal boards on a stacked black plate" style="background:linear-gradient(135deg,#4a6e3f,#2b2b2b)"></div></div><div class="name">KVX RB8-72 w/ P16v3 +</div><div class="sub">Expansion board</div></div>
  <div class="card" style="left:786px;top:2462px"><div class="shot"><div role="img" aria-label="Relay boards on a black mounting plate" style="background:linear-gradient(135deg,#555,#262626)"></div></div><div class="name">KVX RB8-72 w/ P16v3 +</div><div class="sub">Expansion board</div></div>
  <div class="card" style="left:111px;top:2835px"><div class="shot"><div role="img" aria-label="Power supply above controller boards" style="background:linear-gradient(135deg,#bdbdbd,#2e2e2e)"></div></div><div class="name">KVX RB8-72 w/ P16v3 +</div><div class="sub">Expansion board</div></div>
  <div class="card" style="left:449px;top:2835px"><div class="shot"><div role="img" aria-label="Twin power supplies on a mounting plate" style="background:linear-gradient(135deg,#c8c8c8,#3a3a3a)"></div></div><div class="name">KVX RB8-72 w/ P16v3 +</div><div class="sub">Expansion board</div></div>
  <div class="card" style="left:786px;top:2835px"><div class="shot"><div role="img" aria-label="Power supply stacked on a black plate" style="background:linear-gradient(135deg,#b5b5b5,#262626)"></div></div><div class="name">KVX RB8-72 w/ P16v3 +</div><div class="sub">Expansion board</div></div>
  <div class="card" style="left:111px;top:3211px"><div class="shot"><div role="img" aria-label="Hardboard plate with hardware bag" style="background:linear-gradient(135deg,#c49a66,#a57a48)"></div></div><div class="name">KVX RB8-72 w/ P16v3 +</div><div class="sub">Expansion board</div></div>
  <div class="card" style="left:449px;top:3211px"><div class="shot"><div role="img" aria-label="Clear plate with fan and wired boards" style="background:linear-gradient(135deg,#6a6a6a,#2a2a2a)"></div></div><div class="name">KVX RB8-72 w/ P16v3 +</div><div class="sub">Expansion board</div></div>
  <div class="card" style="left:786px;top:3211px"><div class="shot"><div role="img" aria-label="Two-level black plate with boards" style="background:linear-gradient(135deg,#4f6a48,#262626)"></div></div><div class="name">KVX RB8-72 w/ P16v3 +</div><div class="sub">Expansion board</div></div>
</section>

<footer class="site-footer">
  <div class="copy">Copyright 2020 @ vorelmik designer</div>
  <div class="follow">Follow Us :</div>
  <div class="social" style="left:987px" aria-label="Social profile"></div>
  <div class="social" style="left:1042px" aria-label="Video channel"></div>
</footer>

</body>
</html>
```